COMPANY NAME: Bright Harbor Ventures: Task Description: We are a new UK based business with global rea

Target Market

- Personal and professional development – 30-55 age group, corporate leaders, Eastern European and Asian markets
- On-assignment projects – Corporate market – Eastern European and Asian Markets
- Property investment - 35-65 age group, Europe, USA, Australia

What we need

We need logos and brand design for a suite of web platforms (website, twitter and Facebook profile). We would like to have a cohesive and consistent look across all of our online platforms. The design suite must therefore include social media logos, backgrounds and headers. Specifically we are looking for:

a. Facebook header/page design: likely to have a more youthful look

b. Website: Header, background and layout that is responsive to devices, iPhone primarily, then tablet, then PC (we have purchased a website building package from SiteKettle so if you are familiar with one of their themes, it would be great to have a design that fits with a theme you would recommend); Design should be able to accommodate a place to position video in the medium term but an image in the short term.

c. LinkedIn: header/logo; more corporate look

d. Twitter: background/logo

e. Powerpoint template: background and logo - simple and soft background not busy

f. Electronic Newsletter: logo, header and sidebar; simple and soft background not busy

h. Business card: sophisticated and simple

Colors

We have in mind a preference for colors from the purple family, maybe lavender, so as to appeal to all genders and age groups. Though we are happy to go with a recommendation if you think otherwise.

We would like a look that is professional, airy, bright, fresh, futuristic, insightful, friendly.

Ethos of the brand

- experiencing opportunity and being fulfilled in a changing world
- services are facilitated through insights
- support provided through our product, services and tailored approach to coaching/partnerships (which includes private client match-making)
- we are service providers and passionate about quality and modern leadership skills at all stages in life.

The company name is "Bright Harbor Ventures” - our main message is helping people move to the next level - through investments, personal and professional growth.

Some of our messaging

1. International Leadership in a new world.

2. New technology;

3. Informed;

4. Positively Influential

5. Making a difference;

6. Empowered;

7. Risk free investments;

8. Commercial opportunity;

9. Fulfilled living;

10. Carefree and Fun Living;

11. Progression;

12. Open-minded

13. Energy/dynamic

The Business:
The business is to move people very quickly out of situations that hold them back. the situations could be their own personal situations; their career; their jobs; their teams; their ideas; their finances; their financial opportunities. Remove their fears and give them the strategies to take action. The team are international and have 40 years experience between them in this area.

We do want to come across modern and dynamic, customer outcome focussed, building long-term relationships; international.
Updates

Project Deadline Extended
Reason: We have not found the right designs - we are not just looking for a website design but also images and logos. Most images we can see in the designs are stock images - very standard. We need an image which will be the face of the company, like the shop front window. This main image will be used on social media (top image) and also the home page of the website.

Target Market(s)

30-55 years
Eastern Europe; UK; Asia; Africa; Middle East
Personal, Professional, Corporate, and Financial Growth

Industry/Entity Type

Business Service

Contact Information for Business Card

Simple and stylish
the 3 areas of the business on the reverse -

International look - Offices in UK and San Francisco

Company name
web address www.brightharborventure.com
email director@brightharborventure.com
Facebook bright harbor venture
LinkedIn Bright Harbor Venture
Twitter Bright Harbor Venture
Telephone: +44 (0) 768 213 5597

Logo Text

Something that symbolises unlimited growth - probably not text - could use the word INSIGHT in some way

Number of Pages Required

1 page

Colors
e4daeb
f3f1f8
ffffff

Requirements
Must have
• social media symbols and address
• company name
• Melanie Thorpe
• Director
• Telephone +44 (0) 768 213 5597
• Website name www.brightharborventure.co.uk
• Reverse of Card:
• Discreet, Fast, Bright Harbor Consultancy
• Corporate, Professional, Personal & Property Investment
Nice to have
• not too angular; soft lines; not too cluttered (possibly social media on the reverse and just logo, name, number on the front?
Should not have
• too busy

```html
<!DOCTYPE html>
<html lang="en">
<head>
<meta charset="utf-8">
<title>Bright Harbor Ventures – Business Card</title>
<link rel="stylesheet" href="https://fonts.googleapis.com/css2?family=Montserrat:wght@700&family=Open+Sans:wght@400;600&display=swap">
<style>
  :root {
    --canvas-bg: #ece9f1;
    --brand-indigo: #2e1f8c;
    --card-white: #ffffff;
    --ink-navy: #1d1550;
    --ink-grey: #5f5b66;
    --ink-soft: #8d8994;
    --lavender-faint: #eceaf6;
    --on-indigo: #ffffff;
    --card-shadow: 0 10px 28px rgba(40, 30, 80, 0.16);
  }
  * { box-sizing: border-box; margin: 0; padding: 0; }
  html, body {
    width: 1200px;
    height: 804px;
    overflow: hidden;
    background: var(--canvas-bg);
  }
  .sheet {
    width: 1200px;
    height: 804px;
    display: flex;
    align-items: center;
    justify-content: center;
    gap: 60px;
  }
  .card {
    position: relative;
    width: 490px;
    height: 280px;
    border-radius: 4px;
    overflow: hidden;
    box-shadow: var(--card-shadow);
  }
  .brand {
    display: flex;
    align-items: center;
    gap: 8px;
    font-family: "Montserrat", Arial, sans-serif;
    font-weight: 700;
    letter-spacing: 0.02em;
    text-transform: uppercase;
    white-space: nowrap;
  }
  .brand__dot {
    width: 10px;
    height: 10px;
    border-radius: 50%;
    flex: none;
  }

  /* Reverse side */
  .card--reverse {
    background: var(--brand-indigo);
    color: var(--on-indigo);
    font-family: "Open Sans", Arial, sans-serif;
  }
  .card--reverse .brand {
    position: absolute;
    left: 0;
    right: 0;
    top: 96px;
    justify-content: center;
    font-size: 19px;
    color: var(--on-indigo);
  }
  .card--reverse .brand__dot { background: var(--on-indigo); }

  .social-row {
    position: absolute;
    left: 36px;
    right: 36px;
    top: 170px;
    display: flex;
    justify-content: space-between;
    align-items: center;
  }
  .social {
    display: flex;
    align-items: center;
    gap: 6px;
    font-size: 10.5px;
    color: var(--on-indigo);
    white-space: nowrap;
  }
  .social__icon {
    width: 8px;
    height: 8px;
    border-radius: 50%;
    background: var(--on-indigo);
    flex: none;
  }

  /* Front side */
  .card--front {
    background: var(--card-white);
    font-family: "Open Sans", Arial, sans-serif;
  }
  .card__accent {
    position: absolute;
    right: -40px;
    top: -70px;
  }
  .card--front .brand {
    position: absolute;
    left: 30px;
    top: 72px;
    font-size: 14px;
    color: var(--ink-navy);
  }
  .card--front .brand__dot { background: var(--ink-navy); width: 8px; height: 8px; }

  .contact {
    position: absolute;
    left: 44px;
    top: 166px;
  }
  .contact__name {
    font-size: 12.5px;
    font-weight: 600;
    letter-spacing: 0.04em;
    text-transform: uppercase;
    color: var(--ink-grey);
  }
  .contact__role {
    margin-top: 3px;
    font-size: 9.5px;
    color: var(--ink-soft);
  }
  .contact__phone {
    margin-top: 4px;
    font-size: 10.5px;
    color: var(--ink-soft);
    letter-spacing: 0.02em;
  }
</style>
</head>
<body>
  <main class="sheet">
    <section class="card card--reverse" aria-label="Business card reverse">
      <div class="brand"><span class="brand__dot"></span>Bright Harbor Ventures</div>
      <div class="social-row">
        <div class="social social--facebook"><span class="social__icon"></span>fb/brightharborventures</div>
        <div class="social social--linkedin"><span class="social__icon"></span>in/brightharborventures</div>
        <div class="social social--twitter"><span class="social__icon"></span>@brightharborventures</div>
      </div>
    </section>

    <section class="card card--front" aria-label="Business card front">
      <svg class="card__accent" width="170" height="170" viewBox="0 0 170 170" aria-hidden="true">
        <circle cx="85" cy="85" r="78" fill="var(--lavender-faint)"/>
      </svg>
      <div class="brand"><span class="brand__dot"></span>Bright Harbor Ventures</div>
      <div class="contact">
        <p class="contact__name">Melanie Thorpe</p>
        <p class="contact__role">Director</p>
        <p class="contact__phone">+44 (0) 768 213 5597</p>
      </div>
    </section>
  </main>
</body>
</html>
```